Business Card Design needed for start up company Halvora

In need of a new business card designed for a start up company based in Sydney, Halvora is a new start up innovative Company, our mission it to make property accessible for everyday Australian and to become the leading Real Estate platform in Australia. We want it to be fresh and clean.

Industry/Entity Type

Financial

Contact Information for Business Card

Section for Name
Section for Title

HALVORA - The Strength of Pooling
Mobile:
Direct:

Font styles to use
Sans Serif

Colors
33a6d7
0692cd
0255a3
ffffff

Requirements
Must have
• Logo, all business card details

```html
<!DOCTYPE html>
<html lang="en">
<head>
<meta charset="utf-8">
<title>Halvora Business Card</title>
<link rel="stylesheet" href="https://fonts.googleapis.com/css2?family=Montserrat:wght@800&family=Arimo:wght@400;700&display=swap">
<style>
  :root {
    --sky: #33a6d7;
    --blue: #0692cd;
    --navy: #0255a3;
    --ink: #1b3f73;
    --deep: #1a78a8;
    --white: #ffffff;
    --paper-top: #f7f7f7;
    --paper-bottom: #e4e4e4;
    --grey-text: #666a6e;
    --backdrop: #d2d2d2;
  }
  * { margin: 0; padding: 0; box-sizing: border-box; }
  html, body { width: 1200px; height: 965px; overflow: hidden; }
  body {
    background: var(--backdrop);
    position: relative;
    font-family: "Arimo", Arial, sans-serif;
  }
  .card {
    position: absolute;
    left: 277px;
    width: 648px;
    height: 369px;
    border-radius: 40px;
    overflow: hidden;
  }
  .card-front {
    top: 97px;
    background: linear-gradient(180deg, var(--paper-top) 0%, var(--white) 30%, var(--paper-bottom) 100%);
  }
  .card-back {
    top: 502px;
    background: linear-gradient(180deg, #229bd3 0%, var(--deep) 100%);
  }
  .brand-mark {
    position: absolute;
    border-radius: 50%;
  }
  .brand-name {
    position: absolute;
    font-family: "Montserrat", Arial, sans-serif;
    font-weight: 800;
    line-height: 1;
    letter-spacing: -1px;
    white-space: nowrap;
  }
  .card-front .brand-mark {
    left: 63px; top: 128px; width: 80px; height: 80px;
    background: var(--blue);
  }
  .card-front .brand-name {
    left: 152px; top: 145px; font-size: 46px; color: var(--ink);
  }
  .divider {
    position: absolute;
    left: 405px; top: 39px;
    width: 2px; height: 256px;
    background: linear-gradient(180deg, transparent 0%, var(--ink) 20%, var(--ink) 80%, transparent 100%);
  }
  .details {
    position: absolute;
    left: 432px; top: 65px;
  }
  .person-name {
    font-weight: 700;
    font-size: 20px;
    color: var(--blue);
    line-height: 1.1;
  }
  .person-title {
    font-size: 14.5px;
    color: var(--ink);
    margin-top: 2px;
  }
  .contact-list {
    list-style: none;
    margin-top: 30px;
  }
  .contact-list li {
    display: flex;
    align-items: center;
    gap: 10px;
    font-size: 14.5px;
    color: var(--grey-text);
    height: 19px;
  }
  .contact-list svg { width: 15px; height: 15px; flex: none; }
  .address {
    margin-top: 26px;
    font-size: 14.5px;
    line-height: 19px;
    color: var(--grey-text);
  }
  .footer-rule {
    position: absolute;
    left: 0; right: 0; top: 325px;
    height: 4px;
    background: var(--ink);
  }
  .footer-band {
    position: absolute;
    left: 0; right: 0; top: 332px; bottom: 0;
    background: var(--deep);
  }
  .card-back .brand-mark {
    left: 86px; top: 121px; width: 128px; height: 128px;
    background: var(--white);
  }
  .card-back .brand-name {
    left: 232px; top: 157px; font-size: 64px; color: var(--white);
  }
</style>
</head>
<body>
  <section class="card card-front" aria-label="Business card front">
    <span class="brand-mark"></span>
    <span class="brand-name">HALVORA</span>
    <span class="divider"></span>
    <div class="details">
      <p class="person-name">Daniel Reyes</p>
      <p class="person-title">Managing Director</p>
      <ul class="contact-list">
        <li>
          <svg viewBox="0 0 16 16" aria-hidden="true"><rect x="1" y="2" width="4" height="13" rx="1" fill="var(--blue)"/><rect x="6" y="2" width="9" height="13" rx="1" fill="var(--blue)"/><rect x="8" y="4" width="5" height="3" fill="#fff"/><rect x="8" y="9" width="5" height="4" fill="#fff" opacity=".6"/></svg>
          +61 2 5550 1842
        </li>
        <li>
          <svg viewBox="0 0 16 16" aria-hidden="true"><path d="M3 1l3 1 1 4-2 1.5c1 2 2.5 3.5 4.5 4.5L11 10l4 1 1 3-2 2C7 16 0 9 0 3z" fill="var(--blue)"/></svg>
          +61 4 5550 7319
        </li>
        <li>
          <svg viewBox="0 0 16 16" aria-hidden="true"><rect x="0" y="3" width="16" height="11" fill="var(--blue)"/><path d="M1 4l7 5 7-5M1 13l5-4M15 13l-5-4" stroke="#fff" stroke-width="1.2" fill="none"/></svg>
          info@halvora.com
        </li>
        <li>
          <svg viewBox="0 0 16 16" aria-hidden="true"><g fill="none" stroke="var(--blue)" stroke-width="1.2"><circle cx="8" cy="8" r="7"/><ellipse cx="8" cy="8" rx="3" ry="7"/><path d="M1 8h14M2.5 4h11M2.5 12h11"/></g></svg>
          www.halvora.com
        </li>
      </ul>
      <p class="address">Here your company or<br>home address</p>
    </div>
    <span class="footer-rule"></span>
    <span class="footer-band"></span>
  </section>

  <section class="card card-back" aria-label="Business card back">
    <span class="brand-mark"></span>
    <span class="brand-name">HALVORA</span>
  </section>
</body>
</html>
```